We are looking for a new PowerPoint template for our new CI

Hey pixelforum! For 25 years we have been an owner-managed IT system house with tradition, values and a great team. After more than 10 years, we would like to upgrade our company and design the entire CI contemporary and modern. Therefore we are looking for a Powerpoint Template which fits to our logo, the colors and an IT company. Details about our company and our service portfolio can be found on our homepage. We are currently adapting our homepage to the new CI resulting from the logo revision. Homepage: http://stage.rovalnet.example Color codes: Gray = RGB: 4040404040 White = RGB: F5F5F5F5F5 Orange = RGB: F7931E Our slogan: We keep your system running Our address data: Company = Kelmar Systeme GmbH Street = Birkenhang 12 POSTCODE = 61847 City = Burladingen We look forward to your ideas and thank you all in advance.

Target Market(s)

Our target group are companies with 10 to 100 employees from all industrial sectors, eg https://www.fernwald-logistik.example/ https://www.mauler-spedition.example/ https://www.quendt.example/ de /

Colors

Designer to choose colors to be used in the design.

Requirements
Must have
• We are looking for a modern IT design in gray / orange. The basis of the design should be our logo. The template should have two different layouts and three different layouts for content. Our logo and slogan should be clearly visible on the start layout. In addition, an area should be reserved for the name of a speaker and the occasion of the presentation.

```html
<!DOCTYPE html>
<html lang="en">
<head>
<meta charset="utf-8">
<title>Kelmar Systeme – Presentation Template</title>
<link href="https://fonts.googleapis.com/css2?family=Roboto:wght@400;700;900&family=Montserrat:wght@600;800&display=swap" rel="stylesheet">
<style>
:root{
  --orange:#f7931e;
  --gray:#404040;
  --dark:#2b2b2b;
  --blue:#1f6fc5;
  --light:#f5f5f5;
  --canvas:#ebebeb;
  --text:#6f6f6f;
}
*{box-sizing:border-box;margin:0;padding:0}
html,body{width:691px;height:1200px;overflow:hidden;background:var(--canvas);font-family:"Roboto",sans-serif}
.canvas{position:relative;width:691px;height:1200px}
.slide{position:absolute;width:209px;height:118px;background:#fff;overflow:hidden;box-shadow:0 1px 3px rgba(0,0,0,.18)}
.a{position:absolute}
.title{position:absolute;left:0;right:0;text-align:center;font-weight:700;font-size:9px;color:#222}
.tx{font-size:2.4px;line-height:3.3px;color:var(--text)}
.tw{color:#fff}
.b{font-weight:700;color:#222}
.logo{position:absolute;right:7px;top:6px;font-family:"Montserrat",sans-serif;font-weight:800;font-size:4.4px;color:var(--orange);letter-spacing:.2px;display:flex;align-items:center;gap:1.5px}
.logo::before{content:"";width:3px;height:3px;background:var(--gray)}
.foot{position:absolute;left:0;right:0;bottom:0;height:5px;background:var(--orange);font-size:2.2px;color:#fff;line-height:5px;padding-left:4px}
.foot .spk{position:absolute;left:90px}
.foot i{position:absolute;right:7px;top:0;width:13px;height:5px;background:var(--gray)}
.photo{position:absolute}
.ph-dark{background:linear-gradient(135deg,#1e1e1e,#3a3a3a 55%,#5a4630)}
.ph-blue{background:linear-gradient(160deg,#c9d3dc,#5d7185 60%,#2d3b4a)}
.ph-sunset{background:linear-gradient(180deg,#eae6e1,#d98a3d 55%,#2a2620)}
.ph-keys{background:linear-gradient(135deg,#2a2e38,#8a5a38 50%,#1b1d22)}
.ico{position:absolute;border-radius:50%;display:flex;align-items:center;justify-content:center}
.card{position:absolute;border-radius:5px}
.num{position:absolute;font-weight:900;font-size:15px;color:#222}
</style>
</head>
<body>
<main class="canvas">

<!-- Row 1 -->
<section class="slide" style="left:25px;top:19.5px">
  <div class="photo ph-dark" style="inset:0" role="img" aria-label="Server room cabling photograph"></div>
  <div class="a" style="left:0;right:0;top:14px;height:5px;background:var(--orange)"></div>
  <div class="a" style="left:0;right:0;top:19px;height:14px;background:rgba(64,64,64,.92);display:flex;justify-content:center;align-items:center">
    <span style="font-family:Montserrat,sans-serif;font-weight:800;font-size:8px;color:#fff">KELMAR</span>
  </div>
  <div class="title" style="top:60px;color:#fff">PRESENTATION TITLE</div>
  <div class="a tw" style="left:0;right:0;top:73px;text-align:center;font-size:3.6px;font-weight:700">Sub title goes here</div>
</section>

<section class="slide" style="left:244px;top:19.5px">
  <div class="a" style="left:11px;top:6px;font-family:Montserrat,sans-serif;font-weight:800;font-size:11px;color:var(--orange);display:flex;align-items:center;gap:3px"><span style="width:6px;height:6px;background:var(--gray)"></span>KELMAR</div>
  <svg class="a" style="left:0;top:0" width="209" height="118" viewBox="0 0 209 118">
    <polygon points="150,0 209,0 209,118 92,118" fill="#2f2f2f"/>
    <polygon points="209,0 209,62 150,118 118,118" fill="#3a2a1a" opacity=".9"/>
    <polygon points="209,14 209,70 168,118 140,118" fill="var(--orange)" opacity=".85"/>
  </svg>
  <div class="photo ph-keys" style="left:150px;top:20px;width:59px;height:60px;opacity:.55;clip-path:polygon(30% 0,100% 0,100% 100%,0 100%)" role="img" aria-label="Code on a screen"></div>
  <div class="a" style="left:9px;top:52px;font-weight:700;font-size:8.5px;color:#333">PRESENTATION TITLE</div>
  <div class="a" style="left:9px;top:63px;font-size:3.4px;color:var(--orange)">Sub title goes here</div>
</section>

<section class="slide" style="left:463px;top:19.5px">
  <div class="a" style="left:0;right:0;top:0;height:35px;background:var(--orange)"></div>
  <div class="photo ph-blue" style="left:16px;top:13px;width:46px;height:82px" role="img" aria-label="Woman working at a computer"></div>
  <div class="a tw" style="left:16px;top:88px;width:48px;height:8px;background:var(--orange);font-size:3.3px;line-height:8px;padding-left:5px">Header text</div>
  <div class="a tw" style="left:72px;top:15px;font-family:Montserrat,sans-serif;font-weight:800;font-size:13px">WELCOME</div>
  <p class="a tx" style="left:72px;top:42px;width:130px;text-align:justify">Lorem ipsum dolor sit amet, consectetur adipiscing elit, sed do eiusmod tempor incididunt ut labore et dolore magna aliqua. Ut enim ad minim veniam, quis nostrud exercitation ullamco laboris nisi ut aliquip ex ea commodo consequat duis aute irure.</p>
  <p class="a tx" style="left:72px;top:69px;width:130px;text-align:justify">It is a long established fact that a reader will be distracted by the readable content of a page when looking at its layout. The point of using lorem ipsum is a normal distribution of letters, making it look like readable text.</p>
  <div class="foot">Occasion Of The Presentation<span class="spk">NAME OF A SPEAKER</span><i></i></div>
</section>

<!-- Row 2 -->
<section class="slide" style="left:25px;top:150px">
  <div class="logo">KELMAR</div>
  <div class="photo ph-dark" style="left:11px;top:12px;width:79px;height:91px" role="img" aria-label="Laptop with code on a desk"></div>
  <div class="a" style="left:30px;top:30px;width:78px;height:18px;background:rgba(255,255,255,.9);font-family:Montserrat,sans-serif;font-weight:800;font-size:11px;color:var(--orange);line-height:18px;text-align:center">AGENDA</div>
  <div class="a tx" style="left:118px;top:17px;line-height:8.4px;font-family:Georgia,serif;font-size:2.6px;color:#999">
    i.&nbsp;&nbsp;&nbsp;Introduction<br>ii.&nbsp;&nbsp;About Us<br>iii.&nbsp;Welcome Message<br>iv.&nbsp;&nbsp;Company Profile<br>v.&nbsp;&nbsp;&nbsp;Team<br>vi.&nbsp;&nbsp;Team Group<br>vii.&nbsp;Portfolio<br>viii.&nbsp;Info graphic<br>ix.&nbsp;&nbsp;Contact Us<br>x.&nbsp;&nbsp;&nbsp;Data Chart
  </div>
  <div class="foot">Occasion Of The Presentation<span class="spk">NAME OF A SPEAKER</span><i></i></div>
</section>

<section class="slide" style="left:244px;top:150px">
  <svg class="a" style="left:0;top:0" width="209" height="14" viewBox="0 0 209 14">
    <rect width="209" height="8" fill="#2f2f2f"/>
    <polygon points="0,8 140,8 209,2 209,5 148,11 0,11" fill="var(--orange)"/>
  </svg>
  <div class="a tw" style="left:8px;top:2.6px;font-size:2.3px">Name Of A Speaker</div>
  <div class="a" style="right:4px;top:2.6px;font-size:2.3px;color:var(--orange)">Occasion Of The Presentation</div>
  <div class="title" style="top:16px">Four Column Text</div>
  <div class="num" style="left:25px;top:38px">01</div>
  <div class="num" style="left:113px;top:38px">03</div>
  <div class="num" style="left:25px;top:72px;color:var(--orange)">03</div>
  <div class="num" style="left:113px;top:72px">04</div>
  <div class="a tx" style="left:52px;top:40px;width:48px"><b class="b">Stage one</b><br>Lorem ipsum is simply dummy text of the printing and typesetting</div>
  <div class="a tx" style="left:140px;top:40px;width:48px"><b class="b">Stage one</b><br>Lorem ipsum is simply dummy text of the printing and typesetting</div>
  <div class="a tx" style="left:52px;top:74px;width:48px"><b style="color:var(--orange)">Stage one</b><br>Lorem ipsum is simply dummy text of the printing and typesetting</div>
  <div class="a tx" style="left:140px;top:74px;width:48px"><b class="b">Stage one</b><br>Lorem ipsum is simply dummy text of the printing and typesetting</div>
  <div class="foot">KELMAR<span class="spk"></span><i></i></div>
</section>

<section class="slide" style="left:463px;top:150px">
  <div class="logo">KELMAR</div>
  <div class="title" style="top:16px">Four Column Text</div>
  <svg class="a" style="left:0;top:0" width="209" height="118" viewBox="0 0 209 118">
    <circle cx="29" cy="46" r="9" fill="var(--orange)"/>
    <path d="M25 46l3 3 5-6" stroke="#fff" stroke-width="1.2" fill="none"/>
    <circle cx="123" cy="46" r="8.5" fill="#fff" stroke="#ccc" stroke-width=".8"/>
    <path d="M119 46l3 3 5-6" stroke="#555" stroke-width="1" fill="none"/>
    <circle cx="29" cy="81" r="8.5" fill="#fff" stroke="#ccc" stroke-width=".8"/>
    <path d="M25 81l3 3 5-6" stroke="#555" stroke-width="1" fill="none"/>
    <circle cx="123" cy="81" r="8.5" fill="#fff" stroke="#ccc" stroke-width=".8"/>
    <path d="M119 81l3 3 5-6" stroke="#555" stroke-width="1" fill="none"/>
  </svg>
  <div class="a tx" style="left:43px;top:39px;width:55px"><b style="color:var(--orange)">Stage one</b><br><br>Lorem ipsum is simply dummy text of the printing and typesetting</div>
  <div class="a tx" style="left:137px;top:39px;width:55px"><b class="b">Stage three</b><br><br>Lorem ipsum is simply dummy text of the printing and typesetting</div>
  <div class="a tx" style="left:43px;top:74px;width:55px"><b class="b">Stage two</b><br><br>Lorem ipsum is simply dummy text of the printing and typesetting</div>
  <div class="a tx" style="left:137px;top:74px;width:55px"><b class="b">Stage four</b><br><br>Lorem ipsum is simply dummy text of the printing and typesetting</div>
  <div class="foot">Occasion Of The Presentation<span class="spk">NAME OF A SPEAKER</span><i></i></div>
</section>

<!-- Row 3 -->
<section class="slide" style="left:25px;top:281px">
  <div class="logo">KELMAR</div>
  <div class="title" style="left:-40px;top:14px">Leistungsportfolio</div>
  <svg class="a" style="left:6px;top:36px" width="82" height="62" viewBox="0 0 82 62">
    <g fill="#fff" stroke="#e4e4e4" stroke-width=".5">
      <rect x="0" y="0" width="24" height="16" rx="2"/><rect x="28" y="0" width="24" height="16" rx="2"/><rect x="56" y="0" width="24" height="16" rx="2"/>
      <rect x="0" y="21" width="24" height="16" rx="2"/><rect x="28" y="21" width="24" height="16" rx="2"/><rect x="56" y="21" width="24" height="16" rx="2"/>
      <rect x="0" y="42" width="24" height="16" rx="2"/><rect x="28" y="42" width="24" height="16" rx="2"/><rect x="56" y="42" width="24" height="16" rx="2"/>
    </g>
    <rect x="5" y="6" width="14" height="3" fill="#555"/><rect x="33" y="7" width="14" height="2" fill="#bbb"/><circle cx="68" cy="8" r="3" fill="#3b8fd9"/>
    <rect x="7" y="26" width="10" height="6" fill="#d33"/><circle cx="40" cy="29" r="3.5" fill="#8bbf7a"/><rect x="62" y="25" width="12" height="8" fill="#2b5ca8"/>
    <rect x="6" y="48" width="12" height="4" fill="#7a7a7a"/><rect x="34" y="48" width="12" height="4" fill="#e8552b"/><rect x="62" y="48" width="12" height="4" fill="#444"/>
  </svg>
  <div class="a tx" style="left:98px;top:34px;width:108px;line-height:6.4px;color:#555">
    • Administration von Servern und Netzwerken<br>• Hardware und Software<br>• Netzwerktechnik<br>• IT Management und Backup Management<br>• VoIP - Telefonie<br>• Beratung und Projektmanagement<br>• Service und Support vor Ort und per Fernwartung<br>• Autorisierter Reseller und Partner Nordlicht, Wallbrook, Kestrel, u.v.m.<br>• Cloud Backup Service Provider<br>• Webdesign, Webhosting und Mailserver 100% Hosted in Germany
  </div>
  <div class="foot">Occasion Of The Presentation<span class="spk">NAME OF A SPEAKER</span><i></i></div>
</section>

<section class="slide" style="left:244px;top:281px">
  <div class="photo ph-dark" style="left:0;right:0;top:0;height:60px" role="img" aria-label="Dark office workstation"></div>
  <div class="a tw" style="left:16px;top:9px;font-family:Montserrat,sans-serif;font-weight:600;font-size:8.4px;line-height:8.6px">WELCOME TO<br><span style="color:var(--orange)">EXCLUSIVE TEMPLATE</span></div>
  <p class="a tx tw" style="left:16px;top:35px;width:180px;font-size:2.4px">Lorem ipsum is simply dummy text of the printing and typesetting industry. Lorem ipsum has been the industry's standard dummy text ever since the 1500s, when an unknown printer took a galley of type and scrambled it to make a type specimen book. It has survived not only five centuries but also the leap into electronic typesetting, remaining essentially unchanged, popularised with desktop publishing software like Typeset Studio.</p>
  <div class="a" style="left:13px;top:70px;width:59px;height:34px;background:#404040"></div>
  <div class="a" style="left:75px;top:70px;width:59px;height:34px;background:var(--orange)"></div>
  <div class="a" style="left:137px;top:70px;width:59px;height:34px;background:var(--blue)"></div>
  <div class="ico" style="left:37px;top:64px;width:11px;height:11px;background:#404040;border:1px solid #fff"><svg width="6" height="5" viewBox="0 0 6 5"><circle cx="2" cy="1.4" r="1.1" fill="#fff"/><circle cx="4.3" cy="1.6" r=".9" fill="#fff"/><path d="M0 5a2 2 0 0 1 4 0zM3.5 5a1.7 1.7 0 0 1 2.5-1.4V5z" fill="#fff"/></svg></div>
  <div class="ico" style="left:99px;top:64px;width:11px;height:11px;background:var(--orange);border:1px solid #fff"><svg width="6" height="4" viewBox="0 0 6 4"><path d="M2 0L0 2l2 2M4 0l2 2-2 2" stroke="#fff" stroke-width=".8" fill="none"/></svg></div>
  <div class="ico" style="left:161px;top:64px;width:11px;height:11px;background:var(--blue);border:1px solid #fff"><svg width="6" height="6" viewBox="0 0 6 6"><path d="M0 3L6 0 4 6 3 3.6z" fill="#fff"/></svg></div>
  <p class="a tx tw" style="left:16px;top:80px;width:53px;text-align:center;font-size:2.1px;line-height:2.8px">Lorem ipsum is simply dummy text of the printing and typesetting industry, the standard text ever since the 1500s when an unknown printer took a galley.</p>
  <p class="a tx tw" style="left:78px;top:80px;width:53px;text-align:center;font-size:2.1px;line-height:2.8px">Lorem ipsum is simply dummy text of the printing and typesetting industry, the standard text ever since the 1500s when an unknown printer took a galley.</p>
  <p class="a tx tw" style="left:140px;top:80px;width:53px;text-align:center;font-size:2.1px;line-height:2.8px">Lorem ipsum is simply dummy text of the printing and typesetting industry, the standard text ever since the 1500s when an unknown printer took a galley.</p>
  <div class="foot" style="background:#404040">Occasion Of The Presentation<span class="spk">NAME OF A SPEAKER</span><i style="background:#222"></i></div>
</section>

<section class="slide" style="left:463px;top:281px">
  <div class="logo">KELMAR</div>
  <div class="title" style="top:13px">Graph Page</div>
  <p class="a tx" style="left:14px;top:36px;width:84px">Ut wisi enim ad minim veniam, quis nostrud exerci tation ullamcorper suscipit lobortis nisl ut aliquip ex ea commodo consequat.</p>
  <p class="a tx" style="left:14px;top:57px;width:84px">Lorem ipsum dolor sit amet, consectetuer adipiscing elit, sed diam nonummy nibh euismod tincidunt ut laoreet dolore magna aliquam erat volutpat.</p>
  <p class="a tx" style="left:14px;top:79px;width:84px">Ut wisi enim ad minim veniam, quis nostrud exerci tation ullamcorper suscipit lobortis nisl ut aliquip ex ea commodo consequat.</p>
  <svg class="a" style="left:108px;top:30px" width="20" height="70" viewBox="0 0 20 70">
    <polygon points="10,1 18,5.5 18,14.5 10,19 2,14.5 2,5.5" fill="#404040"/>
    <polygon points="10,26 18,30.5 18,39.5 10,44 2,39.5 2,30.5" fill="var(--orange)"/>
    <polygon points="10,50 18,54.5 18,63.5 10,68 2,63.5 2,54.5" fill="#404040"/>
    <g fill="#fff" font-size="3" font-family="Roboto" text-anchor="middle"><text x="10" y="11">01</text><text x="10" y="36">02</text><text x="10" y="60">03</text></g>
  </svg>
  <div class="a tx" style="left:132px;top:33px"><b style="font-family:Montserrat,sans-serif;font-size:4px;color:#222">DESIGN</b><br>There are many variations of passages of lorem.</div>
  <div class="a tx" style="left:132px;top:58px"><b style="font-family:Montserrat,sans-serif;font-size:4px;color:#222">DIGITAL MARKETING</b><br>There are many variations of passages of lorem.</div>
  <div class="a tx" style="left:132px;top:82px"><b style="font-family:Montserrat,sans-serif;font-size:4px;color:#222">SUPPORTING</b><br>There are many variations of passages of lorem.</div>
  <div class="foot">Occasion Of The Presentation<span class="spk">NAME OF A SPEAKER</span><i></i></div>
</section>

<!-- Row 4 -->
<section class="slide" style="left:25px;top:411.5px">
  <div class="logo">KELMAR</div>
  <div class="title" style="left:-60px;top:13px">Graph Page</div>
  <svg class="a" style="left:0;top:0" width="209" height="118" viewBox="0 0 209 118">
    <polygon points="0,63 209,38 209,118 0,118" fill="var(--orange)"/>
    <rect x="14" y="30" width="104" height="64" fill="#1a1a1a"/>
    <rect x="17" y="33" width="98" height="56" fill="#fff"/>
    <path d="M56 94h20l3 8H53z" fill="#bbb"/><rect x="45" y="102" width="42" height="2" fill="#ccc"/>
    <line x1="30" y1="82" x2="108" y2="82" stroke="#ccc" stroke-width=".4"/>
    <rect x="32" y="48" width="6" height="34" fill="var(--blue)"/><rect x="39" y="71" width="6" height="11" fill="var(--orange)"/><rect x="46" y="71" width="6" height="11" fill="#555"/>
    <rect x="70" y="65" width="6" height="17" fill="var(--blue)"/><rect x="77" y="47" width="6" height="35" fill="var(--orange)"/><rect x="84" y="71" width="6" height="11" fill="#555"/>
    <g fill="none" stroke="#fff" stroke-width=".8"><circle cx="120" cy="64" r="3.4"/><circle cx="120" cy="83" r="3.4"/><circle cx="120" cy="101" r="3.4"/></g>
    <g fill="none" stroke="#fff" stroke-width=".7"><path d="M118.4 64l1.2 1.2 2-2.2M118.4 83l1.2 1.2 2-2.2M118.4 101l1.2 1.2 2-2.2"/></g>
  </svg>
  <p class="a tx tw" style="left:127px;top:59px;width:77px">Ut wisi enim ad minim veniam, quis nostrud exerci tation ullamcorper suscipit lobortis nisl ut aliquip ex ea commodo.</p>
  <p class="a tx tw" style="left:127px;top:78px;width:77px">Lorem ipsum dolor sit amet, consectetuer adipiscing elit, sed diam nonummy nibh euismod tincidunt ut laoreet dolore magna.</p>
  <p class="a tx tw" style="left:127px;top:96px;width:77px">Ut wisi enim ad minim veniam, quis nostrud exerci tation ullamcorper suscipit lobortis nisl ut aliquip ex ea commodo.</p>
  <div class="foot">Occasion Of The Presentation<span class="spk">NAME OF A SPEAKER</span><i></i></div>
</section>

<section class="slide" style="left:244px;top:411.5px">
  <div class="logo">KELMAR</div>
  <div class="title" style="left:-60px;top:13px">Graph Page</div>
  <p class="a tx" style="left:8px;top:31px;width:122px;font-size:2.1px;line-height:2.9px">Lorem ipsum the printing and typesetting industry. Lorem ipsum has been the industry's standard dummy text ever since the 1500s, when an unknown printer took a galley of type and scrambled it to make a type.</p>
  <div class="photo" style="left:124px;top:22px;width:85px;height:84px;background:linear-gradient(135deg,#2d2d2d,#1a1a1a)" role="img" aria-label="Laptop showing a brand graphic"></div>
  <div class="a" style="left:120px;top:104px;width:89px;height:3px;background:#ccc"></div>
  <div class="a" style="left:8px;top:49px;width:5px;height:5px;background:var(--orange)"></div>
  <div class="a" style="left:48px;top:49px;width:5px;height:5px;background:#ddd"></div>
  <div class="a" style="left:88px;top:49px;width:5px;height:5px;background:#ddd"></div>
  <div class="a" style="left:8px;top:83px;width:5px;height:5px;background:#777"></div>
  <div class="a" style="left:48px;top:83px;width:5px;height:5px;background:#555"></div>
  <div class="a" style="left:88px;top:83px;width:5px;height:5px;background:#555"></div>
  <p class="a tx" style="left:8px;top:57px;width:36px;font-size:2px;line-height:2.7px">Our mission is delivering creative solution through visual communication we focus on the general</p>
  <p class="a tx" style="left:48px;top:57px;width:36px;font-size:2px;line-height:2.7px">Our mission is delivering creative solution through visual communication we focus on the general</p>
  <p class="a tx" style="left:88px;top:57px;width:36px;font-size:2px;line-height:2.7px">Our mission is delivering creative solution through visual communication we focus on the general</p>
  <p class="a tx" style="left:8px;top:91px;width:36px;font-size:2px;line-height:2.7px">Our mission is delivering creative solution through visual communication we focus on the general</p>
  <p class="a tx" style="left:48px;top:91px;width:36px;font-size:2px;line-height:2.7px">Our mission is delivering creative solution through visual communication we focus on the general</p>
  <p class="a tx" style="left:88px;top:91px;width:36px;font-size:2px;line-height:2.7px">Our mission is delivering creative solution through visual communication we focus on the general</p>
  <div class="foot">Occasion Of The Presentation<span class="spk">NAME OF A SPEAKER</span><i></i></div>
</section>

<section class="slide" style="left:463px;top:411.5px">
  <div class="logo">KELMAR</div>
  <div class="title" style="top:12px">Table</div>
  <svg class="a" style="left:0;top:0" width="209" height="118" viewBox="0 0 209 118">
    <rect x="11" y="27" width="50" height="10" fill="var(--orange)"/>
    <rect x="63" y="27" width="37" height="10" fill="#404040"/>
    <rect x="102" y="27" width="37" height="10" fill="var(--orange)"/>
    <rect x="141" y="27" width="35" height="10" fill="#404040"/>
    <rect x="178" y="27" width="20" height="10" fill="var(--orange)"/>
    <rect x="11" y="47" width="187" height="9" fill="#f2f2f2"/>
    <rect x="11" y="67" width="187" height="9" fill="#f2f2f2"/>
    <rect x="11" y="87" width="187" height="9" fill="#f2f2f2"/>
    <g font-family="Roboto" font-size="3" fill="#fff"><text x="16" y="33.3">Example Title</text><text x="68" y="33.3">Business</text><text x="107" y="33.3">Brand</text><text x="146" y="33.3">Percent</text><text x="181" y="33.3">Quality</text></g>
    <g font-family="Roboto" font-size="2.8" fill="#999">
      <text x="16" y="53">Example One</text><text x="68" y="53">$40</text><text x="107" y="53">$4567</text><text x="146" y="53">45%</text><text x="181" y="53">$80</text>
      <text x="16" y="63">Example Two</text><text x="68" y="63">$320</text><text x="107" y="63">$356</text><text x="146" y="63">60%</text><text x="181" y="63">$320</text>
      <text x="16" y="73">Example Three</text><text x="68" y="73">$120</text><text x="107" y="73">$35</text><text x="146" y="73">40%</text><text x="181" y="73">$120</text>
      <text x="16" y="83">Example Four</text><text x="68" y="83">$2</text><text x="107" y="83">$3567</text><text x="146" y="83">5%</text><text x="181" y="83">$2</text>
      <text x="16" y="93">Example Five</text><text x="68" y="93">$6730</text><text x="107" y="93">$3</text><text x="146" y="93">29%</text><text x="181" y="93">$6730</text>
    </g>
  </svg>
  <div class="foot">Occasion Of The Presentation<span class="spk">NAME OF A SPEAKER</span><i></i></div>
</section>

<!-- Row 5 -->
<section class="slide" style="left:25px;top:542.5px">
  <div class="photo" style="left:0;right:0;top:0;height:60px;background:linear-gradient(180deg,#f7f7f7,#d9d9d9)" role="img" aria-label="Light architectural background"></div>
  <div class="a" style="left:0;right:0;top:60px;bottom:0;background:#404040"></div>
  <div class="title" style="top:14px;font-family:Montserrat,sans-serif;font-weight:600;font-size:8px">VISION, MISSION, VALUES</div>
  <div class="a" style="left:0;right:0;top:25px;text-align:center;font-size:3.6px;font-weight:700;color:var(--orange)">Your subtitle is here</div>
  <div class="card" style="left:13px;top:46px;width:50px;height:59px;background:#fff"></div>
  <div class="card" style="left:77px;top:46px;width:50px;height:59px;background:#fff"></div>
  <div class="card" style="left:141px;top:46px;width:50px;height:59px;background:#fff"></div>
  <svg class="a" style="left:0;top:0" width="209" height="118" viewBox="0 0 209 118">
    <path d="M34 57l8-4-3 8-1.5-3z" fill="var(--orange)"/>
    <ellipse cx="102" cy="57" rx="5" ry="3" fill="none" stroke="var(--orange)" stroke-width="1"/><circle cx="102" cy="57" r="1.5" fill="var(--orange)"/>
    <circle cx="166" cy="55.5" r="2.5" fill="none" stroke="var(--orange)" stroke-width="1.2"/><path d="M164 58l-1 4 3-1 3 1-1-4" fill="var(--orange)"/>
  </svg>
  <div class="a b" style="left:13px;top:66px;width:50px;text-align:center;font-size:3.3px">MISSION</div>
  <div class="a b" style="left:77px;top:66px;width:50px;text-align:center;font-size:3.3px">VISION</div>
  <div class="a b" style="left:141px;top:66px;width:50px;text-align:center;font-size:3.3px">VALUES</div>
  <p class="a tx" style="left:16px;top:74px;width:44px;text-align:center;color:#333">Lorem ipsum dolor sit amet, consectetur adipiscing elit, sed do eiusmod tempor incididunt ut labore et dolore magna aliqua.</p>
  <p class="a tx" style="left:80px;top:74px;width:44px;text-align:center;color:#333">Lorem ipsum dolor sit amet, consectetur adipiscing elit, sed do eiusmod tempor incididunt ut labore et dolore magna aliqua.</p>
  <p class="a tx" style="left:144px;top:74px;width:44px;text-align:center;color:#333">Lorem ipsum dolor sit amet, consectetur adipiscing elit, sed do eiusmod tempor incididunt ut labore et dolore magna aliqua.</p>
</section>

<section class="slide" style="left:244px;top:542.5px">
  <div class="photo" style="left:0;right:0;top:0;height:72px;background:linear-gradient(135deg,#e4e4e4,#f4f4f4 60%,#d0d0d0)" role="img" aria-label="Light office background"></div>
  <div class="a" style="left:0;right:0;top:72px;bottom:0;background:#404040"></div>
  <div class="a" style="left:37px;top:12px;font-weight:700;font-size:9px;color:var(--orange)">Graph Page</div>
  <div class="a" style="left:12px;top:44px;width:6px;height:10px;border:.8px solid var(--orange);border-radius:1px"></div>
  <div class="a" style="left:12px;top:82px;width:8px;height:8px;border:.8px solid var(--orange);border-radius:1px"></div>
  <p class="a tx" style="left:27px;top:35px;width:88px;color:#333"><b class="b">Contents Here</b><br>You can simply impress your audience and add a unique zing and appeal to your presentations. Get a modern template that is beautifully designed. I hope and I believe that this template will save your time, money and reputation.</p>
  <p class="a tx tw" style="left:27px;top:75px;width:88px"><b>Contents Here</b><br>You can simply impress your audience and add a unique zing and appeal to your presentations. Get a modern template that is beautifully designed. I hope and I believe that this template will save your time, money and reputation.</p>
  <div class="a" style="left:124px;top:24px;width:72px;height:48px;background:#1a1a1a;border-radius:2px;padding:2px">
    <div style="width:100%;height:100%;background:#fff;position:relative">
      <svg width="68" height="44" viewBox="0 0 68 44"><rect x="0" y="0" width="10" height="44" fill="#eee"/><g><rect x="30" y="14" width="3" height="10" fill="#e84"/><rect x="33" y="11" width="3" height="13" fill="#4a8"/><rect x="36" y="9" width="3" height="15" fill="#c33"/><rect x="39" y="13" width="3" height="11" fill="#36c"/></g><circle cx="56" cy="14" r="4" fill="none" stroke="#e84" stroke-width="1.5"/><rect x="14" y="30" width="50" height="1" fill="#ddd"/><rect x="14" y="34" width="50" height="1" fill="#ddd"/><rect x="14" y="38" width="50" height="1" fill="#ddd"/></svg>
    </div>
  </div>
  <div class="a" style="left:154px;top:72px;width:12px;height:10px;background:#bbb"></div>
  <div class="a" style="left:145px;top:82px;width:30px;height:2px;background:#999"></div>
</section>

<section class="slide" style="left:463px;top:542.5px">
  <div class="logo">KELMAR</div>
  <div class="title" style="top:14px">Graph Page</div>
  <svg class="a" style="left:0;top:0" width="209" height="118" viewBox="0 0 209 118">
    <g stroke="#404040" stroke-width=".5" stroke-dasharray="1.5 1"><line x1="44" y1="45" x2="67" y2="45"/><line x1="92" y1="45" x2="116" y2="45"/><line x1="141" y1="45" x2="165" y2="45"/></g>
    <circle cx="32" cy="45" r="12" fill="#fde3c2"/><circle cx="32" cy="45" r="9.5" fill="var(--orange)"/>
    <circle cx="80" cy="45" r="12" fill="#cfe0f3"/><circle cx="80" cy="45" r="9.5" fill="var(--blue)"/>
    <circle cx="129" cy="45" r="12" fill="#fde3c2"/><circle cx="129" cy="45" r="9.5" fill="var(--orange)"/>
    <circle cx="177" cy="45" r="12" fill="#cfe0f3"/><circle cx="177" cy="45" r="9.5" fill="var(--blue)"/>
    <path d="M32 39c2 2 2 6 0 9-2-3-2-7 0-9zM30.5 47l-1.5 3 1.5-1M33.5 47l1.5 3-1.5-1" fill="#fff"/>
    <circle cx="80" cy="45" r="4.5" fill="none" stroke="#fff" stroke-width=".9"/><circle cx="80" cy="45" r="2" fill="none" stroke="#fff" stroke-width=".9"/>
    <rect x="125" y="41" width="8" height="8" fill="none" stroke="#fff" stroke-width=".7"/><rect x="126.5" y="45" width="1.3" height="3" fill="#fff"/><rect x="128.5" y="43" width="1.3" height="5" fill="#fff"/><rect x="130.5" y="44" width="1.3" height="4" fill="#fff"/>
    <path d="M173.5 40h7v3a3.5 3.5 0 0 1-7 0zM176 46h2v2.5h2v1.5h-6v-1.5h2z" fill="#fff"/>
    <g font-family="Roboto" font-size="3.1" fill="#888" text-anchor="middle"><text x="32" y="63">ENTER TEXT</text><text x="32" y="67">HERE</text><text x="80" y="63">ENTER TEXT</text><text x="80" y="67">HERE</text><text x="129" y="63">ENTER TEXT</text><text x="129" y="67">HERE</text><text x="177" y="63">ENTER TEXT</text><text x="177" y="67">HERE</text></g>
  </svg>
  <div class="a" style="left:0;right:0;top:85px;bottom:0;background:#404040"></div>
  <p class="a tx tw" style="left:10px;top:96px;width:189px;text-align:center;font-size:3px;line-height:3.7px">Lorem ipsum dolor sit amet, consectetur adipiscing elit, sed do eiusmod tempor incididunt ut labore et dolore magna aliqua. Lorem ipsum dolor sit amet, consectetur adipiscing elit, sed do eiusmod tempor incididunt ut labore et dolore magna aliqua.</p>
</section>

<!-- Row 6 -->
<section class="slide" style="left:25px;top:673px">
  <div class="logo">KELMAR</div>
  <div class="title" style="top:12px">Six Main Stages</div>
  <svg class="a" style="left:0;top:0" width="209" height="118" viewBox="0 0 209 118">
    <g stroke="#bbb" stroke-width=".4" stroke-dasharray="1 1" fill="none"><path d="M60 41q20 0 28 15M60 62h25M60 83q20 0 28-15M149 41q-20 0-28 15M149 62h-25M149 83q-20 0-28-15"/></g>
    <g fill="#999"><circle cx="60" cy="41" r="1.4"/><circle cx="60" cy="62" r="1.4"/><circle cx="60" cy="83" r="1.4"/><circle cx="149" cy="41" r="1.4"/><circle cx="149" cy="62" r="1.4"/><circle cx="149" cy="83" r="1.4"/></g>
    <rect x="89" y="48" width="31" height="31" rx="5" fill="#404040" transform="rotate(45 104.5 63.5)"/>
  </svg>
  <div class="a tw" style="left:82px;top:55px;width:45px;text-align:center;font-size:3.6px">Main stage<div style="font-size:2.1px;line-height:2.9px;margin-top:1px">dummy text of the printing<br>Of the printing and<br>typesetting</div></div>
  <div class="a tx" style="left:16px;top:37px;width:40px;text-align:right"><b class="b" style="font-size:3px">Main example</b><br>Is delivering creative solution<br>Through visual comunication</div>
  <div class="a tx" style="left:16px;top:58px;width:40px;text-align:right"><b class="b" style="font-size:3px">Main example</b><br>Is delivering creative solution<br>Through visual comunication</div>
  <div class="a tx" style="left:16px;top:79px;width:40px;text-align:right"><b class="b" style="font-size:3px">Main example</b><br>Is delivering creative solution<br>Through visual comunication</div>
  <div class="a tx" style="left:158px;top:37px;width:44px"><b class="b" style="font-size:3px">Main example</b><br>Is delivering creative solution<br>Through visual comunication</div>
  <div class="a tx" style="left:158px;top:58px;width:44px"><b class="b" style="font-size:3px">Main example</b><br>Is delivering creative solution<br>Through visual comunication</div>
  <div class="a tx" style="left:158px;top:79px;width:44px"><b class="b" style="font-size:3px">Main example</b><br>Is delivering creative solution<br>Through visual comunication</div>
  <div class="foot">Occasion Of The Presentation<span class="spk">NAME OF A SPEAKER</span><i></i></div>
</section>

<section class="slide" style="left:244px;top:673px">
  <div class="photo ph-sunset" style="left:88px;top:0;width:121px;height:113px" role="img" aria-label="Man standing on a cliff at sunset"></div>
  <p class="a tx" style="left:19px;top:16px;width:46px;text-align:justify;color:#555">Lorem ipsum dolor sit amet, consectetur adipiscing elit. Donec mauris lorem, vestibulum ac rutrum id, feugiat in dui. Donec vitae dapibus tellus. Vestibulum nunc sem, finibus molestie tellus.<br><br>Integer eget auctor nunc. Maecenas tincidunt eleifend consequat. Nulla efficitur urna et massa dapibus maximus. Maecenas sit amet risus pretium, sagittis dui ut, consectetur purus. Phasellus auctor consectetur arcu a consequat. Vestibulum congue sed orci efficitur finibus. Integer malesuada finibus ligula, aliquet lobortis nulla commodo vel.</p>
  <div class="a tw" style="left:75px;top:35px;width:74px;height:38px;background:rgba(247,147,30,.92);font-family:Montserrat,sans-serif;font-weight:800;font-size:8.8px;line-height:12.5px;text-align:center;padding-top:1px">FOLOW<br>YOUR<br>DREAMS</div>
  <div class="foot">Occasion Of The Presentation<span class="spk">NAME OF A SPEAKER</span><i></i></div>
</section>

<section class="slide" style="left:463px;top:673px">
  <div class="logo">KELMAR</div>
  <div class="title" style="top:15px">Our solution</div>
  <p class="a tx" style="left:10px;top:34px;width:189px;text-align:center">Integer eget auctor nunc. Maecenas tincidunt eleifend consequat. Nulla efficitur urna et massa dapibus maximus. Maecenas sit amet risus pretium, sagittis dui ut, consectetur purus. Phasellus auctor consectetur arcu a consequat. Vestibulum congue sed orci efficitur finibus. Integer malesuada finibus ligula, aliquet lobortis nulla commodo vel.</p>
  <svg class="a" style="left:0;top:0" width="209" height="118" viewBox="0 0 209 118">
    <circle cx="16" cy="63" r="5.5" fill="var(--orange)"/><g fill="#fff"><rect x="13.5" y="62" width="1" height="3"/><rect x="15.5" y="60.5" width="1" height="4.5"/><rect x="17.5" y="61.5" width="1" height="3.5"/></g>
    <circle cx="115" cy="63" r="5.5" fill="#404040"/><circle cx="114.5" cy="62.5" r="2" fill="none" stroke="#fff" stroke-width=".8"/><path d="M116 64l1.6 1.6" stroke="#fff" stroke-width=".8"/>
    <circle cx="16" cy="89" r="5.5" fill="#404040"/><circle cx="16" cy="88" r="2" fill="#fff"/><rect x="15.2" y="90" width="1.6" height="1.6" fill="#fff"/>
    <circle cx="115" cy="89" r="5.5" fill="var(--orange)"/><circle cx="115" cy="89" r="2.4" fill="none" stroke="#fff" stroke-width="1.1" stroke-dasharray="1 .6"/>
  </svg>
  <div class="a tx" style="left:27px;top:56px;width:75px"><b class="b" style="font-size:3px">CONTENTS TITLE</b><br>Lorem ipsum dolor sit amet, consectetur adipiscing elit, sed do eiusmod tempor incididunt ut labore et dolore magna aliqua.</div>
  <div class="a tx" style="left:126px;top:56px;width:75px"><b class="b" style="font-size:3px">CONTENTS TITLE</b><br>Lorem ipsum dolor sit amet, consectetur adipiscing elit, sed do eiusmod tempor incididunt ut labore et dolore magna aliqua.</div>
  <div class="a tx" style="left:27px;top:82px;width:75px"><b class="b" style="font-size:3px">CONTENTS TITLE</b><br>Lorem ipsum dolor sit amet, consectetur adipiscing elit, sed do eiusmod tempor incididunt ut labore et dolore magna aliqua.</div>
  <div class="a tx" style="left:126px;top:82px;width:75px"><b class="b" style="font-size:3px">CONTENTS TITLE</b><br>Lorem ipsum dolor sit amet, consectetur adipiscing elit, sed do eiusmod tempor incididunt ut labore et dolore magna aliqua.</div>
  <div class="foot">Occasion Of The Presentation<span class="spk">NAME OF A SPEAKER</span><i></i></div>
</section>

<!-- Row 7 -->
<section class="slide" style="left:25px;top:803.5px">
  <div class="a" style="left:0;top:0;width:122px;height:61px;background:#fff"></div>
  <div class="a" style="left:0;top:4px;width:6px;height:52px;background:var(--orange)"></div>
  <div class="a" style="left:11px;top:19px;font-weight:700;font-size:10.5px;line-height:12.5px;color:#404040">Client Case<br>Study Slide</div>
  <div class="photo" style="left:122px;top:0;width:87px;height:61px;background:radial-gradient(ellipse at 50% 55%,#d8613a,#5a1e40 40%,#111 75%)" role="img" aria-label="Backlit laptop keyboard"></div>
  <div class="a" style="left:0;top:61px;width:122px;height:52px;background:#f3f3f3"></div>
  <div class="a" style="left:122px;top:61px;width:87px;height:52px;background:var(--orange)"></div>
  <p class="a tx" style="left:10px;top:74px;width:104px;text-align:justify;color:#555">Lorem ipsum dolor sit amet, consectetur adipiscing elit, sed do eiusmod tempor incididunt ut labore et dolore magna aliqua. Lorem ipsum dolor sit amet, consectetur adipiscing elit, sed do eiusmod tempor incididunt ut labore et dolore magna aliqua. Ut enim ad minim veniam, quis nostrud exercitation ullamco laboris nisi ut aliquip ex ea commodo consequat.</p>
  <p class="a tx tw" style="left:132px;top:74px;width:70px;text-align:justify">Lorem ipsum dolor sit amet, consectetur adipiscing elit, sed do eiusmod tempor incididunt ut labore et dolore magna aliqua. Lorem ipsum dolor sit amet, consectetur adipiscing elit.</p>
  <div class="foot">Occasion Of The Presentation<span class="spk">NAME OF A SPEAKER</span><i></i></div>
</section>

<section class="slide" style="left:244px;top:803.5px">
  <div class="logo">KELMAR</div>
  <div class="title" style="top:14px">Three factors &amp; conclusion</div>
  <svg class="a" style="left:0;top:0" width="209" height="118" viewBox="0 0 209 118">
    <path d="M16 78A30 30 0 0 1 53 44" fill="none" stroke="var(--orange)" stroke-width="11"/>
    <polygon points="52,36 62,45 51,52" fill="var(--orange)"/>
    <path d="M66 52A30 30 0 0 1 64 91" fill="none" stroke="#404040" stroke-width="11"/>
    <polygon points="72,88 60,100 58,86" fill="#404040"/>
    <path d="M52 103A30 30 0 0 1 18 88" fill="none" stroke="var(--blue)" stroke-width="11"/>
    <polygon points="10,88 25,80 22,95" fill="var(--blue)"/>
    <circle cx="44" cy="73" r="12" fill="#fff"/>
    <path d="M44 66l4 5-5 3z" fill="#404040"/><path d="M44 80l-4-5 5-3z" fill="var(--orange)"/>
    <g stroke="var(--orange)" stroke-width=".6"><line x1="88" y1="34" x2="88" y2="46"/><line x1="88" y1="52" x2="88" y2="64"/><line x1="88" y1="70" x2="88" y2="82"/></g>
  </svg>
  <div class="a tx" style="left:93px;top:35px;width:108px;color:#444"><span style="font-size:3.3px">Step One Title</span><br>A company is an association or collection of individuals, whether natural persons, legal persons, or a mixture of both. Company</div>
  <div class="a tx" style="left:93px;top:53px;width:108px;color:#444"><span style="font-size:3.3px">Step One Title</span><br>A company is an association or collection of individuals, whether natural persons, legal persons, or a mixture of both. Company</div>
  <div class="a tx" style="left:93px;top:71px;width:108px;color:#444"><span style="font-size:3.3px">Step One Title</span><br>A company is an association or collection of individuals, whether natural persons, legal persons, or a mixture of both. Company</div>
  <p class="a tx" style="left:89px;top:96px;width:112px;color:#444">A company is an association or collection of individuals, whether natural persons, legal persons, or a mixture of both. Company</p>
  <div class="foot">Occasion Of The Presentation<span class="spk">NAME OF A SPEAKER</span><i></i></div>
</section>

<section class="slide" style="left:463px;top:803.5px">
  <div class="logo">KELMAR</div>
  <div class="title" style="top:16px">Three factors</div>
  <div class="card" style="left:21px;top:42px;width:50px;height:50px;background:var(--orange)"></div>
  <div class="card" style="left:80px;top:42px;width:50px;height:50px;background:#404040"></div>
  <div class="card" style="left:139px;top:42px;width:50px;height:50px;background:var(--blue)"></div>
  <svg class="a" style="left:0;top:0" width="209" height="118" viewBox="0 0 209 118">
    <g fill="#fff" stroke="#e6e6e6" stroke-width=".6"><circle cx="46" cy="42" r="7"/><circle cx="105" cy="42" r="7"/><circle cx="164" cy="42" r="7"/></g>
    <path d="M42.5 43l7-3.5-2.5 7-1.2-2.3z" fill="#333"/>
    <g fill="#333"><rect x="102" y="41" width="1" height="3"/><rect x="104" y="39" width="1" height="5"/><rect x="106" y="40" width="1" height="4"/><rect x="101.5" y="44.3" width="6.5" height=".6"/></g>
    <circle cx="164" cy="42" r="2.6" fill="none" stroke="#333" stroke-width="1.2" stroke-dasharray="1 .7"/>
  </svg>
  <p class="a tx tw" style="left:28px;top:61px;width:36px;text-align:center">Business valuation is a process and a set of procedures used to estimate the economic value of an owner's interest in a business.</p>
  <p class="a tx tw" style="left:87px;top:61px;width:36px;text-align:center">Business valuation is a process and a set of procedures used to estimate the economic value of an owner's interest in a business.</p>
  <p class="a tx tw" style="left:146px;top:61px;width:36px;text-align:center">Business valuation is a process and a set of procedures used to estimate the economic value of an owner's interest in a business.</p>
  <div class="foot">Occasion Of The Presentation<span class="spk">NAME OF A SPEAKER</span><i></i></div>
</section>

<!-- Row 8 -->
<section class="slide" style="left:25px;top:934px">
  <div class="logo">KELMAR</div>
  <div class="title" style="top:15px">Our Team</div>
  <svg class="a" style="left:0;top:0" width="209" height="118" viewBox="0 0 209 118" role="img" aria-label="Team member portraits">
    <g fill="#404040"><circle cx="36" cy="47" r="8.5"/><circle cx="82" cy="47" r="8.5"/><circle cx="128" cy="47" r="8.5"/><circle cx="174" cy="47" r="8.5"/><circle cx="36" cy="82" r="8.5"/><circle cx="82" cy="82" r="8.5"/><circle cx="128" cy="82" r="8.5"/><circle cx="174" cy="82" r="8.5"/></g>
    <g font-family="Georgia, serif" font-size="2.3" fill="#666" text-anchor="middle">
      <text x="36" y="60">Lena Marwick</text><text x="36" y="63">Founder &amp; CEO</text>
      <text x="82" y="60">Tara Brunn</text><text x="82" y="63">Partner</text>
      <text x="128" y="60">Jonas Feller</text><text x="128" y="63">Partner</text>
      <text x="174" y="60">Mira Holt</text><text x="174" y="63">Founder &amp; CEO</text>
      <text x="36" y="95">Paul Renner</text><text x="36" y="98">Founder &amp; CEO</text>
      <text x="82" y="95">Ida Sommer</text><text x="82" y="98">Partner</text>
      <text x="128" y="95">Nils Brandt</text><text x="128" y="98">Partner</text>
      <text x="174" y="95">Vera Kolb</text><text x="174" y="98">Partner</text>
    </g>
  </svg>
  <div class="foot">Occasion Of The Presentation<span class="spk">NAME OF A SPEAKER</span><i></i></div>
</section>

<section class="slide" style="left:244px;top:934px">
  <div class="logo">KELMAR</div>
  <div class="title" style="top:14px">Professionelles IT Managment</div>
  <svg class="a" style="left:0;top:0" width="209" height="118" viewBox="0 0 209 118">
    <rect x="25" y="32" width="49" height="5" fill="#404040"/><rect x="75" y="29" width="50" height="8" fill="var(--orange)"/><rect x="126" y="32" width="49" height="5" fill="#404040"/>
    <rect x="25" y="37" width="49" height="14" fill="#e6e6e6"/><rect x="75" y="37" width="50" height="14" fill="#fbb664"/><rect x="126" y="37" width="49" height="14" fill="#e6e6e6"/>
    <rect x="25" y="51" width="49" height="52" fill="#f7f7f7"/><rect x="75" y="51" width="50" height="52" fill="#f7f7f7"/><rect x="126" y="51" width="49" height="52" fill="#f7f7f7"/>
    <g font-family="Georgia, serif" font-size="3" fill="#fff" text-anchor="middle"><text x="49.5" y="35.8">Private Plan</text><text x="100" y="33.6">Business Plan</text><text x="150.5" y="35.8">Mega Plan</text></g>
    <g font-family="Georgia, serif" font-size="9" text-anchor="middle"><text x="46" y="47" fill="#555">20<tspan font-size="4" dy="-3">$</tspan></text><text x="96" y="47" fill="#fff">30<tspan font-size="4" dy="-3">$</tspan></text><text x="147" y="47" fill="#555">50<tspan font-size="4" dy="-3">$</tspan></text></g>
    <g font-family="Georgia, serif" font-size="2.2" font-style="italic"><text x="52" y="48" fill="#888">Per month</text><text x="102" y="48" fill="#fff">Per month</text><text x="153" y="48" fill="#888">Per month</text></g>
    <g id="checks" stroke="var(--orange)" stroke-width=".9" fill="none">
      <path d="M27 57.5l1.3 1.3 2-2.4M27 65.5l1.3 1.3 2-2.4M27 73.5l1.3 1.3 2-2.4M27 81.5l1.3 1.3 2-2.4M27 89.5l1.3 1.3 2-2.4"/>
      <path d="M78 57.5l1.3 1.3 2-2.4M78 65.5l1.3 1.3 2-2.4M78 73.5l1.3 1.3 2-2.4M78 81.5l1.3 1.3 2-2.4M78 89.5l1.3 1.3 2-2.4"/>
      <path d="M129 57.5l1.3 1.3 2-2.4M129 65.5l1.3 1.3 2-2.4M129 73.5l1.3 1.3 2-2.4M129 81.5l1.3 1.3 2-2.4M129 89.5l1.3 1.3 2-2.4"/>
    </g>
    <g stroke="#555" stroke-width=".8"><path d="M27.5 96l2.5 2.5M30 96l-2.5 2.5M78.5 96l2.5 2.5M81 96l-2.5 2.5M129.5 96l2.5 2.5M132 96l-2.5 2.5"/></g>
    <g font-family="Roboto" font-size="2.4" fill="#666">
      <text x="33" y="59">Fernwartungssoftware</text><text x="33" y="67">Gerätedokumentation</text><text x="33" y="75">Monitoring</text><text x="33" y="83">Patchmanagement</text><text x="33" y="91">Internet Content Filter</text><text x="33" y="99">Mobile Device Management</text>
      <text x="84" y="59">Fernwartungssoftware</text><text x="84" y="67">Gerätedokumentation</text><text x="84" y="75">Monitoring</text><text x="84" y="83">Patchmanagement</text><text x="84" y="91">Internet Content Filter</text><text x="84" y="99">Mobile Device Management</text>
      <text x="135" y="59">Fernwartungssoftware</text><text x="135" y="67">Gerätedokumentation</text><text x="135" y="75">Monitoring</text><text x="135" y="83">Patchmanagement</text><text x="135" y="91">Internet Content Filter</text><text x="135" y="99">Mobile Device Management</text>
    </g>
  </svg>
  <div class="foot">Occasion Of The Presentation<span class="spk">NAME OF A SPEAKER</span><i></i></div>
</section>

<section class="slide" style="left:463px;top:934px">
  <div class="logo">KELMAR</div>
  <div class="title" style="top:15px">List Text Sample</div>
  <svg class="a" style="left:0;top:0" width="209" height="118" viewBox="0 0 209 118">
    <rect x="16" y="40" width="36" height="12" fill="var(--orange)"/><rect x="52" y="39" width="141" height="14" fill="#fff" stroke="#e8e8e8" stroke-width=".5"/>
    <rect x="16" y="56" width="36" height="12" fill="#404040"/><rect x="52" y="55" width="141" height="14" fill="#fff" stroke="#e8e8e8" stroke-width=".5"/>
    <rect x="16" y="72" width="36" height="12" fill="var(--orange)"/><rect x="52" y="71" width="141" height="14" fill="#fff" stroke="#e8e8e8" stroke-width=".5"/>
    <rect x="16" y="88" width="36" height="12" fill="#404040"/><rect x="52" y="87" width="141" height="14" fill="#fff" stroke="#e8e8e8" stroke-width=".5"/>
    <g font-family="Roboto" font-size="2.4" fill="#fff" text-anchor="middle"><text x="34" y="47">Business valuation</text><text x="34" y="63">Business valuation</text><text x="34" y="79">Business valuation</text><text x="34" y="95">Business valuation</text></g>
  </svg>
  <p class="a tx" style="left:55px;top:41px;width:136px;font-size:2px;line-height:2.7px;color:#555">Lorem ipsum dolor sit amet, consectetur adipiscing elit, sed do eiusmod tempor incididunt ut labore et dolore magna aliqua. Lorem ipsum dolor sit amet, consectetur adipiscing elit, sed do eiusmod tempor incididunt ut labore.</p>
  <p class="a tx" style="left:55px;top:57px;width:136px;font-size:2px;line-height:2.7px;color:#555">Lorem ipsum dolor sit amet, consectetur adipiscing elit, sed do eiusmod tempor incididunt ut labore et dolore magna aliqua. Lorem ipsum dolor sit amet, consectetur adipiscing elit, sed do eiusmod tempor incididunt ut labore.</p>
  <p class="a tx" style="left:55px;top:73px;width:136px;font-size:2px;line-height:2.7px;color:#555">Lorem ipsum dolor sit amet, consectetur adipiscing elit, sed do eiusmod tempor incididunt ut labore et dolore magna aliqua. Lorem ipsum dolor sit amet, consectetur adipiscing elit, sed do eiusmod tempor incididunt ut labore.</p>
  <p class="a tx" style="left:55px;top:89px;width:136px;font-size:2px;line-height:2.7px;color:#555">Lorem ipsum dolor sit amet, consectetur adipiscing elit, sed do eiusmod tempor incididunt ut labore et dolore magna aliqua. Lorem ipsum dolor sit amet, consectetur adipiscing elit, sed do eiusmod tempor incididunt ut labore.</p>
  <div class="foot">Occasion Of The Presentation<span class="spk">NAME OF A SPEAKER</span><i></i></div>
</section>

<!-- Row 9 -->
<section class="slide" style="left:147px;top:1060px">
  <div class="logo">KELMAR</div>
  <div class="title" style="left:-60px;top:14px">Text and Picture</div>
  <p class="a tx" style="left:17px;top:31px;width:88px;text-align:justify;line-height:3.6px">Lorem ipsum the printing and typesetting industry. Lorem ipsum has been the industry's standard dummy text ever since the 1500s, when an unknown printer took a galley of type and scrambled it to make a type specimen book. It has survived not only five centuries, but also the leap into electronic typesetting, remaining essentially unchanged. It was popularised in the 1960s with the release. It is a long established fact that a reader will be distracted by the readable content. Lorem ipsum the printing and typesetting industry. Lorem ipsum has been the industry's standard dummy text ever since the 1500s, when an unknown printer took a galley of type and scrambled it to make a type specimen book.</p>
  <div class="a" style="left:97px;top:30px;width:47px;height:36px;background:var(--orange)"></div>
  <p class="a tx tw" style="left:103px;top:35px;width:36px;font-size:2.1px;line-height:3.2px">Section text<br><br>Our mission is delivering creative solution through visual communication we focus</p>
  <div class="a" style="left:97px;top:66px;width:47px;height:47px;background:#f4f4f4"></div>
  <p class="a tx" style="left:103px;top:74px;width:36px;font-size:2.1px;line-height:3.2px">Section text<br><br>Our mission is delivering creative solution through visual communication we focus</p>
  <div class="photo ph-keys" style="left:144px;top:30px;width:65px;height:83px" role="img" aria-label="Close-up of illuminated keyboard"></div>
  <div class="foot">Occasion Of The Presentation<span class="spk">NAME OF A SPEAKER</span><i></i></div>
</section>

<section class="slide" style="left:367px;top:1060px">
  <div class="photo ph-dark" style="left:0;right:0;top:0;height:82px;background:linear-gradient(135deg,#2a2a2a,#4a4a4a 60%,#333)" role="img" aria-label="Dark office interior"></div>
  <div class="a tw" style="left:33px;top:30px;font-family:Montserrat,sans-serif;font-weight:600;font-size:10px">ABOUT US</div>
  <svg class="a" style="left:0;top:0" width="209" height="118" viewBox="0 0 209 118">
    <g fill="var(--orange)" stroke="#fff" stroke-width="1.4"><circle cx="30" cy="84" r="9"/><circle cx="77" cy="84" r="9"/><circle cx="127" cy="84" r="9"/><circle cx="173" cy="84" r="9"/></g>
    <g fill="none" stroke="#fff" stroke-width=".7"><circle cx="30" cy="84" r="4"/><ellipse cx="30" cy="84" rx="1.8" ry="4"/><line x1="26" y1="84" x2="34" y2="84"/></g>
    <path d="M74 80.5c.6-.6 1.2-.4 1.6.2l.8 1.3c.3.5 0 1-.4 1.3.5 1.2 1.4 2.1 2.6 2.6.3-.4.8-.7 1.3-.4l1.3.8c.6.4.8 1 .2 1.6-1.2 1.2-3 .8-4.8-1s-3.8-4.2-2.6-6.4z" fill="#fff"/>
    <rect x="123" y="81.5" width="8" height="5.5" fill="#fff"/><path d="M123 81.5l4 3 4-3" stroke="var(--orange)" stroke-width=".6" fill="none"/>
    <path d="M173 89c-2.5-3-3.5-4.5-3.5-6a3.5 3.5 0 0 1 7 0c0 1.5-1 3-3.5 6z" fill="#fff"/><circle cx="173" cy="83" r="1.2" fill="var(--orange)"/>
    <g font-family="Roboto" font-size="2.5" fill="#333" text-anchor="middle"><text x="30" y="100">www.kelmar-systeme.example</text><text x="77" y="100">0555 018 274</text><text x="127" y="100">info@kelmar-systeme.example</text><text x="173" y="100">Here to write your,</text><text x="173" y="103.5">Company adress</text></g>
  </svg>
  <div class="foot">Occasion Of The Presentation<span class="spk">NAME OF A SPEAKER</span><i></i></div>
</section>

</main>
</body>
</html>
```